Italian restaurant needs new site

Need to make our website better.

Must have reservation module

Must be able to sell wine tasting tours and wine pairing tours and intégrate with dunmo desk

Blog

Social media

Wandervane ranking and last review.
Updates

Number of Pages Required

1 page

Font styles to use
Serif

Requirements
Must have
• Reservation module
• Marketplace to buy wine pairings and gift certificates
• Wandervane review
• Kindlepost posts
• All info from old site

```html
<!DOCTYPE html>
<html lang="en">
<head>
<meta charset="utf-8">
<title>Verdello Bistro – Italian Restaurant in Cabo San Lucas</title>
<link href="https://fonts.googleapis.com/css2?family=Cinzel:wght@400;700&family=Lato:wght@400;700&display=swap" rel="stylesheet">
<style>
:root{
  --maroon:#7d0f1c;
  --ink:#1c1c1c;
  --text:#4a4a4a;
  --muted:#8a8a8a;
  --line:#dcdcdc;
  --paper:#ffffff;
  --night:#0d0d0d;
  --card-grey:#e4e4e4;
}
*{box-sizing:border-box;margin:0;padding:0}
html,body{width:1200px;height:4852px;overflow:hidden}
body{font-family:"Lato",Arial,sans-serif;color:var(--text);background:var(--paper);position:relative;font-size:14px;line-height:1.5}
.heading{font-family:"Cinzel",Georgia,serif;color:var(--ink);font-weight:400}
section,header,footer,.topbar{position:absolute;left:0;width:1200px}
.btn{display:inline-block;background:var(--maroon);color:#fff;font-size:13px;padding:6px 16px;text-transform:uppercase;letter-spacing:.5px}
.photo{position:absolute}
.underline{display:block;width:70px;height:3px;background:var(--maroon);margin:10px auto 0}

/* top bar */
.topbar{top:0;height:45px;border-bottom:1px solid var(--line)}
.social{position:absolute;display:flex;gap:8px}
.social span{width:22px;height:22px;border-radius:50%;background:var(--maroon);display:block}
.topbar .social{left:168px;top:11px}
.top-phone{position:absolute;left:480px;top:12px;font-size:14px;color:var(--ink);display:flex;align-items:center;gap:6px;white-space:nowrap}
.top-cta{position:absolute;top:0;height:45px;color:#fff;font-size:12px;text-transform:uppercase;display:flex;align-items:center;gap:8px;padding:0 14px;white-space:nowrap}
.top-cta.gift{left:640px;width:195px;background:var(--maroon)}
.top-cta.reserve{left:835px;width:205px;background:var(--ink)}

/* header */
.site-header{top:45px;height:133px}
.brand{position:absolute;left:160px;top:32px;display:flex;align-items:center;gap:10px}
.brand-mark{width:14px;height:14px;border-radius:50%;background:var(--maroon)}
.brand-name{font-family:"Cinzel",Georgia,serif;font-size:26px;color:var(--maroon);font-weight:700;line-height:1}
.brand-tag{position:absolute;left:184px;top:72px;font-size:10px;color:var(--muted);letter-spacing:1px;text-transform:uppercase}
.nav{position:absolute;right:160px;top:52px;display:flex;gap:48px;font-size:15px;color:var(--ink)}
.nav .active{color:var(--maroon);border-bottom:2px solid var(--maroon);padding-bottom:4px}

/* hero */
.hero{top:178px;height:512px;background:linear-gradient(100deg,#2a2420 0%,#3b2a22 35%,#1a1614 70%,#0f0d0c 100%)}
.hero .photo{left:0;top:0;width:1200px;height:512px;background:linear-gradient(100deg,rgba(184,83,42,.55) 0%,rgba(120,60,30,.35) 45%,transparent 65%)}
.hero-title{position:absolute;left:740px;top:190px;color:#fff;font-family:"Cinzel",Georgia,serif;font-size:34px;line-height:1.3;text-align:center}
.slider-arrow{position:absolute;top:235px;width:28px;height:40px;background:rgba(255,255,255,.25)}

/* welcome */
.welcome{top:690px;height:426px}
.welcome h2{position:absolute;left:160px;top:56px;font-size:32px}
.welcome .rule{position:absolute;left:160px;top:104px;width:80px;height:3px;background:var(--maroon)}
.welcome .lead{position:absolute;left:160px;top:122px;width:560px;font-weight:700;color:var(--ink);font-size:14px}
.welcome .body{position:absolute;left:160px;top:172px;width:580px;font-size:12.5px;line-height:1.7}
.welcome .btn{position:absolute;left:160px;top:345px}
.welcome .photo{left:770px;top:50px;width:280px;height:320px;background:linear-gradient(160deg,#f4ead0 0%,#e0c57a 45%,#a8485a 100%)}

/* reservation */
.reservation{top:1132px;height:453px;background:linear-gradient(90deg,#2b1d18,#4a3227 50%,#2b1d18)}
.reservation .photo{inset:0}
.booking{position:absolute;left:430px;top:80px;width:430px;height:290px;background:rgba(0,0,0,.72);padding:22px 28px;color:#fff}
.booking h3{font-family:"Cinzel",Georgia,serif;font-size:24px;text-align:center;font-weight:400}
.booking .underline{width:60px;margin-bottom:18px}
.fields{display:grid;grid-template-columns:1fr 1fr;gap:10px}
.field{height:32px;border:1px solid #888;background:rgba(255,255,255,.08);font-size:12px;padding:7px 8px;display:flex;justify-content:space-between}
.field.wide{grid-column:1/3;height:46px}
.submit{display:block;width:230px;margin:16px auto 0;background:var(--maroon);text-align:center;font-family:"Cinzel",Georgia,serif;font-size:18px;padding:4px 0}

/* menu */
.menu{top:1585px;height:631px}
.menu h2{position:absolute;left:0;width:1200px;top:72px;font-size:32px;text-align:center}
.menu h2 b{color:var(--maroon);font-weight:400}
.feature{position:absolute;left:160px;top:160px;width:352px;height:330px;background:linear-gradient(160deg,#3a3632,#1d1b19);border:6px solid #d8d8d8}
.feature-label{position:absolute;left:0;width:100%;top:130px;text-align:center;color:#fff}
.feature-label h4{font-family:"Cinzel",Georgia,serif;font-size:24px;font-weight:400}
.feature-label p{font-size:11px;padding:0 60px;color:#ddd}
.feature .plus{position:absolute;left:157px;top:210px;width:26px;height:26px;border:2px solid #fff;border-radius:50%}
.menu-item{position:absolute;left:556px;width:580px;height:100px}
.menu-item .photo{left:0;top:0;width:112px;height:100px}
.menu-item h4{position:absolute;left:138px;top:-4px;font-family:"Cinzel",Georgia,serif;font-size:22px;font-weight:400;color:var(--ink)}
.menu-item p{position:absolute;left:138px;top:30px;width:430px;font-size:11.5px;line-height:1.6}
.menu .btn{position:absolute;left:566px;top:526px}

/* atmosphere */
.atmosphere{top:2216px;height:462px;background:linear-gradient(180deg,#2a1c18,#3a2620 50%,#1a1210)}
.atmosphere .photo{inset:0}
.atmosphere .inner{position:absolute;left:160px;top:130px;width:880px;text-align:center;color:#fff}
.atmosphere h2{font-family:"Cinzel",Georgia,serif;font-size:40px;font-weight:400}
.atmosphere .sub{font-weight:700;font-size:16px;margin-top:6px}
.atmosphere .body{font-size:13px;margin:8px auto 0;width:780px;color:#e8e8e8}
.atmosphere .btn{margin-top:24px}

/* blog */
.blog{top:2678px;height:712px}
.blog h2{position:absolute;left:0;width:1200px;top:60px;text-align:center;font-size:32px}
.blog h2 b{color:var(--maroon);font-weight:400}
.blog .intro{position:absolute;left:160px;top:124px;width:880px;text-align:center;font-size:12.5px}
.post{position:absolute;top:212px;width:280px;height:380px;background:var(--card-grey)}
.post .photo{left:0;top:0;width:280px;height:200px}
.post .pin{position:absolute;left:128px;top:-12px;width:24px;height:24px;border-radius:50%;background:#fff;border:2px solid var(--maroon)}
.post h4{position:absolute;left:16px;top:222px;font-family:"Cinzel",Georgia,serif;font-size:17px;font-weight:400;color:var(--ink)}
.post p{position:absolute;left:16px;top:250px;width:248px;font-size:11px;line-height:1.5}
.post .meta{position:absolute;left:16px;top:328px;font-size:11px;color:var(--ink)}
.post.highlight{background:var(--maroon)}
.post.highlight h4,.post.highlight p,.post.highlight .meta{color:#fff}
.dots{position:absolute;left:568px;top:620px;display:flex;gap:8px}
.dots span{width:12px;height:12px;border-radius:50%;background:#555}
.dots span:first-child{background:var(--maroon)}

/* testimonials */
.customers{top:3390px;height:460px;background:linear-gradient(90deg,#1e1715,#3a2a24 60%,#1e1715)}
.customers .photo{inset:0}
.customers h2{position:absolute;left:0;width:1200px;top:64px;text-align:center;color:#fff;font-family:"Cinzel",Georgia,serif;font-size:32px;font-weight:400}
.avatars{position:absolute;left:0;width:1200px;top:135px;display:flex;justify-content:center;gap:40px}
.avatar{width:100px;text-align:center;color:#ddd;font-size:12px;font-style:italic}
.avatar .ring{width:90px;height:90px;border-radius:50%;border:3px solid #c9a24a;background:linear-gradient(135deg,#9a7a60,#4a362c);margin:0 auto 6px}
.quote{position:absolute;left:160px;top:298px;width:880px;height:112px;background:rgba(255,255,255,.18);color:#eee;font-style:italic;font-size:13px;text-align:center;padding:18px 40px}
.customers .slider-arrow{top:120px}

/* wine tours */
.tours{top:3850px;height:653px}
.tours h2{position:absolute;left:0;width:1200px;top:66px;text-align:center;font-size:32px}
.tours h2 b{color:var(--maroon);font-weight:400}
.tours .intro{position:absolute;left:200px;top:122px;width:800px;text-align:center;font-size:12.5px}
.tour{position:absolute;top:222px;width:420px;height:380px;border:1px solid var(--line);box-shadow:0 2px 6px rgba(0,0,0,.12);text-align:center}
.tour .photo{left:10px;top:10px;width:398px;height:200px;border:3px solid var(--maroon)}
.tour h4{position:absolute;left:0;width:100%;top:232px;font-family:"Cinzel",Georgia,serif;font-size:24px;font-weight:400;color:var(--ink)}
.tour p{position:absolute;left:30px;width:360px;top:276px;font-size:12px;line-height:1.6}

/* footer */
.site-footer{top:4503px;height:349px;background:var(--night);color:#bbb;font-size:12px}
.site-footer h5{font-family:"Cinzel",Georgia,serif;font-size:17px;color:#fff;font-weight:400;margin-bottom:14px}
.site-footer h5 b{color:var(--maroon);font-weight:400}
.fcol{position:absolute;top:54px}
.fcol ul{list-style:none;line-height:1.9}
.feed{display:flex;gap:10px;margin-bottom:12px}
.feed .thumb{width:44px;height:44px;background:#333;flex:none}
.feed p{font-size:11px;line-height:1.4;width:200px}
.bottom-bar{position:absolute;left:0;top:317px;width:1200px;height:32px;border-top:1px solid #333;font-size:11px}
.bottom-bar .copy{position:absolute;left:160px;top:8px}
.bottom-bar .follow{position:absolute;right:160px;top:5px;display:flex;align-items:center;gap:8px}
.bottom-bar .social{position:static}
.bottom-bar .social span{width:20px;height:20px}
</style>
</head>
<body>

<div class="topbar">
  <div class="social"><span></span><span></span><span></span><span></span></div>
  <div class="top-phone">
    <svg width="16" height="16" viewBox="0 0 24 24"><path d="M6.6 10.8a15 15 0 0 0 6.6 6.6l2.2-2.2c.3-.3.7-.4 1-.2 1.1.4 2.3.6 3.6.6.6 0 1 .4 1 1V20c0 .6-.4 1-1 1A17 17 0 0 1 3 4c0-.6.4-1 1-1h3.5c.6 0 1 .4 1 1 0 1.3.2 2.5.6 3.6.1.3 0 .7-.2 1z" fill="#7d0f1c"/></svg>
    123-456-7890
  </div>
  <div class="top-cta gift">
    <svg width="16" height="16" viewBox="0 0 24 24"><rect x="3" y="9" width="18" height="12" fill="none" stroke="#fff" stroke-width="2"/><path d="M12 9v12M3 9h18" stroke="#fff" stroke-width="2"/></svg>
    Buy Gift Certificates
  </div>
  <div class="top-cta reserve">
    <svg width="16" height="16" viewBox="0 0 24 24"><rect x="3" y="5" width="18" height="16" fill="none" stroke="#fff" stroke-width="2"/><path d="M3 10h18M8 3v4M16 3v4" stroke="#fff" stroke-width="2"/></svg>
    Online Reservation
  </div>
</div>

<header class="site-header">
  <div class="brand"><span class="brand-mark"></span><span class="brand-name">Verdello Bistro</span></div>
  <div class="brand-tag">Italian Cuisine &amp; Wine Bar</div>
  <nav class="nav">
    <span class="active">Home</span><span>About Us</span><span>Menu</span><span>Gallery</span><span>Blog</span><span>Contact Us</span>
  </nav>
</header>

<section class="hero">
  <div class="photo" role="img" aria-label="Margherita pizza on a dark wooden table with a glass of red wine"></div>
  <div class="hero-title">Verdello Bistro<br>Italian Restaurant<br>in Cabo San Lucas</div>
  <div class="slider-arrow" style="left:0"></div>
  <div class="slider-arrow" style="right:0"></div>
</section>

<section class="welcome">
  <h2 class="heading">Welcome To <span style="color:var(--maroon)">Verdello Bistro</span></h2>
  <span class="rule"></span>
  <p class="lead">Lorem ipsum dolor sit amet, consectetuer adipiscing elit, sed diam nonummy nibh euismod tincidunt ut laoreet dolore magna aliquam erat.</p>
  <p class="body">Lorem ipsum dolor sit amet, consectetuer adipiscing elit, sed diam nonummy nibh euismod tincidunt ut laoreet dolore magna aliquam erat volutpat. Ut wisi enim ad minim veniam, quis nostrud exerci tation ullamcorper suscipit lobortis nisl ut aliquip ex ea commodo consequat. Duis autem vel eum iriure dolor in hendrerit in vulputate velit esse molestie consequat, vel illum dolore eu feugiat nulla facilisis at vero eros et accumsan et iusto odio dignissim qui blandit praesent luptatum zzril delenit augue duis dolore te feugait nulla facilisi. Lorem ipsum dolor sit amet, consectetuer adipiscing elit.</p>
  <span class="btn">Read More</span>
  <div class="photo" role="img" aria-label="Wine bottles, glasses of red and white wine, grapes and cheese"></div>
</section>

<section class="reservation">
  <div class="photo" role="img" aria-label="Guests smiling and dining together in the restaurant"></div>
  <div class="booking">
    <h3>Book Online Reservation</h3>
    <span class="underline"></span>
    <div class="fields">
      <div class="field">Name *<span>&#9787;</span></div>
      <div class="field">Phone *<span>&#9742;</span></div>
      <div class="field">Email *<span>&#9993;</span></div>
      <div class="field">No. of Guest *<span>&#9776;</span></div>
      <div class="field wide">Message*<span>&#9998;</span></div>
    </div>
    <span class="submit">Submit</span>
  </div>
</section>

<section class="menu">
  <h2 class="heading">Our <b>Menu Items</b></h2>
  <div class="feature" role="img" aria-label="Shelves of premium beer bottles behind a bar">
    <div class="feature-label">
      <h4>Premium Beer</h4>
      <p>Ut wisi enim ad minim veniam, quis nostrud exerci tation ullamcorper suscipit lobortis.</p>
    </div>
    <span class="plus"></span>
  </div>
  <div class="menu-item" style="top:150px">
    <div class="photo" role="img" aria-label="Chocolate dessert on a plate" style="background:linear-gradient(135deg,#6b3a22,#2e1a10)"></div>
    <h4>Desserts</h4>
    <p>Ut wisi enim ad minim veniam, quis nostrud exerci tation ullamcorper suscipit lobortis nisl ut aliquip ex ea commodo consequat. Duis autem vel eum iriure dolor in hendrerit in vulputate.</p>
  </div>
  <div class="menu-item" style="top:262px">
    <div class="photo" role="img" aria-label="Cup of coffee with latte art" style="background:linear-gradient(135deg,#c8a47a,#5a3a22)"></div>
    <h4>Coffees</h4>
    <p>Ut wisi enim ad minim veniam, quis nostrud exerci tation ullamcorper suscipit lobortis nisl ut aliquip ex ea commodo consequat. Duis autem vel eum iriure dolor in hendrerit in vulputate.</p>
  </div>
  <div class="menu-item" style="top:374px">
    <div class="photo" role="img" aria-label="Evening cocktails at the bar" style="background:linear-gradient(135deg,#c07a2a,#3a1e10)"></div>
    <h4>Nightcap</h4>
    <p>Ut wisi enim ad minim veniam, quis nostrud exerci tation ullamcorper suscipit lobortis nisl ut aliquip ex ea commodo consequat. Duis autem vel eum iriure dolor in hendrerit in vulputate.</p>
  </div>
  <span class="btn">View More</span>
</section>

<section class="atmosphere">
  <div class="photo" role="img" aria-label="Candle-lit dining room with set tables"></div>
  <div class="inner">
    <h2>Unforgettable Atmosphere</h2>
    <p class="sub">Lorem Ipsum Dolor Sit Amet, Consectetuer Adipiscing Elit, Sed Diam Nonummy</p>
    <p class="body">Ut wisi enim ad minim veniam, quis nostrud exerci tation ullamcorper suscipit lobortis nisl ut aliquip ex ea commodo consequat. Duis autem vel eum iriure dolor in hendrerit in vulputate velit esse molestie consequat.</p>
    <span class="btn">Online Reservations</span>
  </div>
</section>

<section class="blog">
  <h2 class="heading">Latest <b>Blog Posts</b></h2>
  <p class="intro">Lorem ipsum dolor sit amet, consectetuer adipiscing elit, sed diam nonummy nibh euismod tincidunt ut laoreet dolore magna aliquam erat volutpat. Ut wisi enim ad minim veniam, quis nostrud exerci tation ullamcorper suscipit lobortis nisl ut aliquip ex ea commodo consequat. Duis autem vel eum iriure dolor.</p>
  <article class="post highlight" style="left:160px">
    <div class="photo" role="img" aria-label="Smoked salmon appetiser on a plate" style="background:linear-gradient(135deg,#e6834a,#9a3a1e)"></div>
    <span class="pin"></span>
    <h4>Lorem Ipsum Dolor</h4>
    <p>Lorem ipsum dolor sit amet, consectetuer adipiscing elit, sed diam nonummy nibh euismod tincidunt ut laoreet dolore magna.</p>
    <div class="meta">By : Sed ut perspiciatis &nbsp;|&nbsp; 0 Comments</div>
  </article>
  <article class="post" style="left:460px">
    <div class="photo" role="img" aria-label="Bowl of pasta with herbs" style="background:linear-gradient(135deg,#d8b86a,#5a4a2a)"></div>
    <span class="pin"></span>
    <h4>Lorem Ipsum Dolor</h4>
    <p>Lorem ipsum dolor sit amet, consectetuer adipiscing elit, sed diam nonummy nibh euismod tincidunt ut laoreet dolore magna.</p>
    <div class="meta">By : Sed ut perspiciatis &nbsp;|&nbsp; 0 Comments</div>
  </article>
  <article class="post" style="left:760px">
    <div class="photo" role="img" aria-label="Baked lasagna with tomato sauce" style="background:linear-gradient(135deg,#d86a30,#8a2a14)"></div>
    <span class="pin"></span>
    <h4>Lorem Ipsum Dolor</h4>
    <p>Lorem ipsum dolor sit amet, consectetuer adipiscing elit, sed diam nonummy nibh euismod tincidunt ut laoreet dolore magna.</p>
    <div class="meta">By : Sed ut perspiciatis &nbsp;|&nbsp; 0 Comments</div>
  </article>
  <div class="dots"><span></span><span></span><span></span><span></span></div>
</section>

<section class="customers">
  <div class="photo" role="img" aria-label="Diners enjoying an evening at the restaurant"></div>
  <h2>Our Happy Customers</h2>
  <div class="avatars">
    <div class="avatar"><div class="ring" role="img" aria-label="Customer portrait"></div>Lorem Ipsum</div>
    <div class="avatar"><div class="ring" role="img" aria-label="Customer portrait"></div>Lorem Ipsum</div>
    <div class="avatar"><div class="ring" role="img" aria-label="Customer portrait"></div>Lorem Ipsum</div>
  </div>
  <div class="slider-arrow" style="left:210px"></div>
  <div class="slider-arrow" style="right:210px"></div>
  <div class="quote">" Lorem ipsum dolor sit amet, consectetuer adipiscing elit, sed diam nonummy nibh euismod tincidunt ut laoreet dolore magna aliquam erat volutpat. Ut wisi enim ad minim veniam, quis nostrud exerci tation ullamcorper suscipit lobortis nisl ut aliquip ex ea commodo consequat. Duis autem vel eum iriure dolor in hendrerit in vulputate velit esse molestie consequat. "</div>
</section>

<section class="tours">
  <h2 class="heading">Wine <b>Tours</b></h2>
  <p class="intro">Lorem ipsum dolor sit amet, consectetuer adipiscing elit, sed diam nonummy nibh euismod tincidunt ut laoreet dolore magna aliquam erat volutpat. Ut wisi enim ad minim veniam, quis nostrud exerci tation ullamcorper suscipit lobortis nisl ut aliquip ex ea commodo consequat.</p>
  <article class="tour" style="left:160px">
    <div class="photo" role="img" aria-label="Couple tasting wine at a vineyard table" style="background:linear-gradient(135deg,#c8d8a0,#6a7a4a 50%,#8a4a3a)"></div>
    <h4>Wine Tasting Tours</h4>
    <p>Lorem ipsum dolor sit amet, consectetuer adipiscing elit, sed diam nonummy nibh euismod tincidunt. Ut wisi enim ad minim veniam, quis nostrud exerci tation ullamcorper.</p>
  </article>
  <article class="tour" style="left:620px">
    <div class="photo" role="img" aria-label="Wine bottle and glasses with cheese pairing" style="background:linear-gradient(135deg,#d8902a,#6a2a10 60%,#1a0a06)"></div>
    <h4>Wine Pairing Tours</h4>
    <p>Lorem ipsum dolor sit amet, consectetuer adipiscing elit, sed diam nonummy nibh euismod tincidunt. Ut wisi enim ad minim veniam, quis nostrud exerci tation ullamcorper.</p>
  </article>
</section>

<footer class="site-footer">
  <div class="fcol" style="left:160px">
    <h5>Quick <b>Links</b></h5>
    <ul><li>› Home</li><li>› About Us</li><li>› Menu</li><li>› Gallery</li><li>› Blog</li><li>› Contact Us</li></ul>
  </div>
  <div class="fcol" style="left:360px">
    <h5>Contact <b>Details</b></h5>
    <p style="line-height:1.6"><span style="color:#fff">VERDELLO BISTRO</span><br>Calle Marina 214, Centro<br>Cabo San Lucas, Mexico</p>
    <p style="margin-top:18px;color:#fff">&#9742; 123-456-7890</p>
    <p style="margin-top:18px">&#9993; info@verdellobistro.com</p>
  </div>
  <div class="fcol" style="left:640px">
    <h5>Kindlepost <b>Feeds</b></h5>
    <div class="feed"><div class="thumb"></div><p><span style="color:#fff">Post Title</span><br>August is the month of the harvest in the valley.</p></div>
    <div class="feed"><div class="thumb"></div><p><span style="color:#fff">Post Title</span><br>August is the month of the harvest in the valley.</p></div>
    <div class="feed"><div class="thumb"></div><p><span style="color:#fff">Post Title</span><br>August is the month of the harvest in the valley.</p></div>
  </div>
  <div class="bottom-bar">
    <span class="copy">Copyright © 2017 Verdello Bistro. All Rights Reserved.</span>
    <span class="follow">FOLLOW US : <span class="social"><span></span><span></span><span></span><span></span></span></span>
  </div>
</footer>

</body>
</html>
```